Small Cosmetics Business needs a label design

We need a label design to affix on our cosmetic products made in Norfolk, England. The label needs to have the manufacturer's name, the product name, an ingredients list, an indication of use (ritual), contact details of manufacturer, weight, period after opening logo, batch number. We would like the label to highlight (in the form of sticker or tags) that the products are 100% natural, that they are hand made, that they do not contain preservatives or chemicals.Attached is a file with typical information for the label. The label should have colours, clarity and evoke nature, luxury.

Target Market(s)

UK

Industry/Entity Type

Cosmetics

Logo Text

Tesori Buna, Shape Radiance

Font styles to use
Decorative

```html
<!DOCTYPE html>
<html lang="en">
<head>
<meta charset="utf-8">
<title>Tesori Buna – Velvet Bloom Label</title>
<link rel="stylesheet" href="https://fonts.googleapis.com/css2?family=Great+Vibes&family=Yellowtail&family=Open+Sans:wght@400;700&display=swap">
<style>
  :root {
    --paper: #ffffff;
    --teal-deep: #6fb3ae;
    --teal-mid: #8cc6c2;
    --teal-light: #b9dedb;
    --magenta: #ec008c;
    --sun-yellow: #fff200;
    --cream: #fbf3c4;
  }
  html, body {
    margin: 0;
    padding: 0;
    width: 1200px;
    height: 848px;
    overflow: hidden;
    background: var(--paper);
  }
  .label-canvas {
    display: block;
    width: 1200px;
    height: 848px;
  }
  .label-disc-pattern { fill: url(#tealSwirlTone); }
  .brand-dot { fill: var(--cream); }
  .brand-name {
    font-family: "Great Vibes", cursive;
    font-size: 50px;
    fill: var(--magenta);
  }
  .product-name {
    font-family: "Yellowtail", cursive;
    font-size: 100px;
    fill: var(--magenta);
    stroke: var(--sun-yellow);
    stroke-width: 5px;
    paint-order: stroke fill;
    stroke-linejoin: round;
  }
  .claims-ring {
    font-family: "Open Sans", sans-serif;
    font-weight: 700;
    font-size: 11.5px;
    fill: var(--magenta);
  }
  .natural-badge-burst {
    fill: var(--magenta);
    stroke: var(--sun-yellow);
    stroke-width: 3px;
    stroke-linejoin: miter;
  }
  .natural-badge-percent {
    font-family: "Open Sans", sans-serif;
    font-weight: 700;
    font-size: 30px;
    fill: var(--sun-yellow);
  }
  .natural-badge-word {
    font-family: "Open Sans", sans-serif;
    font-weight: 400;
    font-size: 14px;
    fill: var(--sun-yellow);
  }
</style>
</head>
<body>
<svg class="label-canvas" viewBox="0 0 1200 848" xmlns="http://www.w3.org/2000/svg">
  <defs>
    <radialGradient id="tealSwirlTone" cx="45%" cy="40%" r="70%">
      <stop offset="0%" stop-color="var(--teal-light)"/>
      <stop offset="55%" stop-color="var(--teal-mid)"/>
      <stop offset="100%" stop-color="var(--teal-deep)"/>
    </radialGradient>
    <path id="claimsArc" d="M 374,470 A 228 228 0 0 0 826,470"/>
  </defs>

  <!-- Label disc with swirl-pattern area -->
  <circle class="label-disc-pattern" cx="600" cy="424" r="244"
          role="img" aria-label="Soft teal background with decorative swirling leaf pattern"/>

  <!-- Brand -->
  <circle class="brand-dot" cx="600" cy="240" r="22"/>
  <text class="brand-name" x="600" y="330" text-anchor="middle">Tesori Buna</text>

  <!-- Product -->
  <text class="product-name" x="597" y="462" text-anchor="middle"
        textLength="454" lengthAdjust="spacingAndGlyphs">Velvet Bloom</text>

  <!-- 100% Natural badge -->
  <g class="natural-badge" transform="translate(600 560)">
    <polygon class="natural-badge-burst"
      points="0,-66 7.3,-58.3 17.1,-63.8 21.8,-53.7 32.9,-57.2 33.5,-45.2 45,-45 42.2,-33.6 53.6,-29.9 47.3,-19.3 57.2,-13 47.8,-5.2 57.9,3.3 46.5,7.4 53.5,18.3 41.4,21.2 44.9,32.8 32.7,33 32.5,45.1 21.2,41.5 17.1,52.8 8.6,44.1 0,53.6 -8.6,44.1 -17.1,52.8 -21.2,41.5 -32.5,45.1 -32.7,33 -44.9,32.8 -41.4,21.2 -53.5,18.3 -46.5,7.4 -57.9,3.3 -47.8,-5.2 -57.2,-13 -47.3,-19.3 -53.6,-29.9 -42.2,-33.6 -45,-45 -33.5,-45.2 -32.9,-57.2 -21.8,-53.7 -17.1,-63.8 -7.3,-58.3"/>
    <g transform="rotate(-15)">
      <text class="natural-badge-percent" x="2" y="4" text-anchor="middle">100%</text>
      <text class="natural-badge-word" x="4" y="22" text-anchor="middle">Natural</text>
    </g>
  </g>

  <!-- Curved claims line -->
  <text class="claims-ring">
    <textPath href="#claimsArc" startOffset="50%" text-anchor="middle"
              textLength="600" lengthAdjust="spacing">Handmade In Norfolk Handmade In Norfolk Contains No Preservatives And No Chemicals</textPath>
  </text>
</svg>
</body>
</html>
```